Business Card Design

Business Card for professional consulting firm working with large financial institutions.

Target Market(s)

Executive buyers

Industry/Entity Type

Banking

Contact Information for Business Card

Mild creativity wanted. Not boring, but do elaborate artwork.

Font styles to use
Serif
Sans Serif

Colors

Designer to choose colors to be used in the design.

Requirements
Must have
• Standard business card features - company name, individual name, telephone, website, email, locations.
Nice to have
• Two colors
Should not have
• too many colors, fancy printing, cartoons.

```html
<!DOCTYPE html>
<html lang="en">
<head>
<meta charset="utf-8">
<title>Northvale Business Card</title>
<link href="https://fonts.googleapis.com/css2?family=Montserrat:wght@400;600;700&family=Lora:wght@400&display=swap" rel="stylesheet">
<style>
  :root {
    --backdrop: #3a3a3c;
    --ink: #111111;
    --paper: #ffffff;
    --mid-grey: #b5b5b5;
    --text-dark: #2a2a2a;
  }
  * { margin: 0; padding: 0; box-sizing: border-box; }
  html, body { width: 1200px; height: 1000px; overflow: hidden; }
  body {
    background: var(--backdrop);
    position: relative;
    font-family: "Montserrat", Arial, sans-serif;
  }
  .card {
    position: absolute;
    left: 300px;
    width: 600px;
    height: 343px;
    border-radius: 22px;
    overflow: hidden;
  }
  .card-back {
    top: 105px;
    background: var(--ink);
    display: flex;
    align-items: center;
    justify-content: center;
  }
  .brand-name {
    font-family: "Lora", Georgia, serif;
    font-weight: 400;
    font-size: 56px;
    color: var(--paper);
    letter-spacing: 1px;
  }
  .card-front {
    top: 520px;
    background: var(--paper);
  }
  .card-front svg { position: absolute; inset: 0; }
  .person { position: absolute; left: 40px; top: 60px; color: var(--text-dark); }
  .person-name { font-weight: 700; font-size: 17px; letter-spacing: 1px; }
  .person-title { font-weight: 400; font-size: 10.5px; letter-spacing: 1px; margin-top: 2px; }
  .address {
    position: absolute; left: 40px; top: 122px;
    font-weight: 600; font-size: 11.5px; line-height: 1.45; color: var(--text-dark);
  }
  .front-brand {
    position: absolute; right: 44px; top: 86px;
    font-family: "Lora", Georgia, serif; font-size: 40px; color: var(--text-dark);
  }
  .contacts {
    position: absolute; right: 22px; top: 266px;
    list-style: none; color: var(--paper);
    font-weight: 600; font-size: 13px; line-height: 20px;
  }
  .contacts li { display: flex; align-items: center; justify-content: flex-end; gap: 10px; }
  .contacts svg { position: static; width: 12px; height: 12px; }
</style>
</head>
<body>
  <section class="card card-back">
    <span class="brand-name">Northvale</span>
  </section>

  <section class="card card-front">
    <svg viewBox="0 0 600 343" width="600" height="343" aria-hidden="true">
      <path d="M0,178 C70,208 170,222 255,214 C170,238 70,232 0,210 Z" fill="var(--mid-grey)"/>
      <path d="M0,248 C120,276 250,256 360,236 C450,220 530,226 600,236 L600,343 L0,343 Z" fill="var(--ink)"/>
      <path d="M45,246 C150,268 300,246 430,232 C310,256 160,282 45,246 Z" fill="var(--paper)"/>
    </svg>
    <div class="person">
      <div class="person-name">DANIEL HART</div>
      <div class="person-title">GENERAL MANAGER</div>
    </div>
    <div class="address">48 Harbor Street Meridian Plaza<br>12th Floor Lakeport, Oregon 97401</div>
    <div class="front-brand">Northvale</div>
    <ul class="contacts">
      <li>+541-555-0187
        <svg viewBox="0 0 12 12"><path d="M3 1 L5 3.5 L4 5 C5 7 6 8 7.5 8.5 L9 7.5 L11 9.5 L9.5 11 C5 10.5 1.5 7 1 2.5 Z" fill="var(--paper)"/></svg>
      </li>
      <li>info@northvale.us
        <svg viewBox="0 0 12 12"><rect x="1" y="2.5" width="10" height="7" fill="none" stroke="var(--paper)" stroke-width="1.2"/><path d="M1 2.5 L6 6.5 L11 2.5" fill="none" stroke="var(--paper)" stroke-width="1.2"/></svg>
      </li>
      <li>www.northvale.us
        <svg viewBox="0 0 12 12"><circle cx="6" cy="6" r="5" fill="none" stroke="var(--paper)" stroke-width="1.1"/><ellipse cx="6" cy="6" rx="2.2" ry="5" fill="none" stroke="var(--paper)" stroke-width="1"/><path d="M1 6 H11" stroke="var(--paper)" stroke-width="1"/></svg>
      </li>
    </ul>
  </section>
</body>
</html>
```